Business Card Design Project

This is the first time we use our new logo. We need a business card that we can use both on our institutional corporate relationships and also that works for our staff that deals with consumers directly.

VELUNDA is a new company dedicated to empower consumers and to provide them with the best choices for specialized health care using the latest telemedicine technology (medicine at a distance via videoconference).

We want to print this cards in high quality materials and process. We will like designs that allow us to use UV spot varnish and other techniques that will differentiate us.

We are including Two different versions of Color logos. In addition we are including white over black background logos. Those can be used replacing the black for a color.

Please note this is the first time we will be creating any corporate materials with our new logo and colors.

Target Market(s)

34+ consumers of medium high and high socioeconomic levels.

Industry/Entity Type

Health

Requirements
Must have
• Our logo on its original colors
Should not have
• Any other graphical element or design that is not our logo

```html
<!DOCTYPE html>
<html lang="en">
<head>
<meta charset="utf-8">
<title>VELUNDA Business Card</title>
<link rel="stylesheet" href="https://fonts.googleapis.com/css2?family=Jost:wght@500;600&family=Arimo:wght@400;700&display=swap">
<style>
  :root {
    --page: #e9ecef;
    --card: #ffffff;
    --ink-navy: #1d5887;
    --ink-text: #2b2f33;
    --sky: #5ab4de;
    --ocean: #1e6db3;
    --teal: #1aa89a;
    --rule: #d5d9dd;
  }
  * { margin: 0; padding: 0; box-sizing: border-box; }
  html, body { width: 1200px; height: 1057px; overflow: hidden; }
  body { background: var(--page); position: relative; font-family: "Arimo", Arial, sans-serif; }

  .card {
    position: absolute;
    left: 200px;
    width: 800px;
    height: 457px;
    background: var(--card);
    box-shadow: 0 6px 18px rgba(0,0,0,0.15);
    overflow: hidden;
  }
  .card--front { top: 50px; }
  .card--back { top: 550px; }

  .header-band {
    position: absolute;
    left: 300px;
    top: 0;
    width: 500px;
    height: 190px;
    background: linear-gradient(180deg, var(--sky) 0%, var(--sky) 50%, var(--ocean) 100%);
  }

  .holder { position: absolute; right: 40px; top: 22px; text-align: right; color: #fff; }
  .holder__name { font-weight: 700; font-size: 26px; }
  .holder__title { font-size: 17px; margin-top: 2px; }

  .wordmark { display: flex; align-items: center; gap: 18px; color: var(--ink-navy); font-family: "Jost", sans-serif; font-weight: 600; letter-spacing: 4px; }
  .wordmark__dot { border-radius: 50%; background: var(--teal); flex: none; }

  .card--front .wordmark { position: absolute; left: 70px; top: 230px; font-size: 64px; }
  .card--front .wordmark__dot { width: 46px; height: 46px; }

  .contacts { position: absolute; left: 80px; top: 345px; list-style: none; font-size: 19px; color: var(--ink-text); }
  .contacts li { display: flex; align-items: center; gap: 10px; line-height: 24px; }
  .contacts svg { width: 16px; height: 16px; flex: none; }

  .divider { position: absolute; left: 470px; top: 345px; width: 1px; height: 96px; background: var(--rule); }

  .address { position: absolute; left: 500px; top: 362px; font-size: 19px; line-height: 26px; color: var(--ink-text); font-style: normal; }

  .card--back .wordmark { position: absolute; left: 50%; top: 170px; transform: translateX(-50%); font-size: 88px; }
  .card--back .wordmark__dot { width: 60px; height: 60px; }
  .site { position: absolute; left: 0; right: 0; top: 300px; text-align: center; font-size: 26px; letter-spacing: 7px; color: var(--ink-text); }
  .site__domain { color: var(--ink-navy); font-weight: 700; }
</style>
</head>
<body>

<section class="card card--front" aria-label="Business card front">
  <div class="header-band" role="img" aria-label="Decorative blue folded-corner graphic area"></div>

  <div class="holder">
    <div class="holder__name">Your Name</div>
    <div class="holder__title">Title</div>
  </div>

  <div class="wordmark">
    <span class="wordmark__dot"></span>
    <span class="wordmark__name">VELUNDA</span>
  </div>

  <ul class="contacts">
    <li>
      <svg viewBox="0 0 16 16" aria-hidden="true"><circle cx="8" cy="8" r="7" fill="none" stroke="var(--ink-navy)" stroke-width="1.4"/><path d="M5.5 4.5c-.8.8-.5 3 1.5 5s4.2 2.3 5 1.5l-1.4-1.4-1.2.6-2.6-2.6.6-1.2z" fill="var(--ink-navy)"/></svg>
      012-345-6789
    </li>
    <li>
      <svg viewBox="0 0 16 16" aria-hidden="true"><circle cx="8" cy="8" r="7" fill="none" stroke="var(--ink-navy)" stroke-width="1.4"/><path d="M5.5 4.5c-.8.8-.5 3 1.5 5s4.2 2.3 5 1.5l-1.4-1.4-1.2.6-2.6-2.6.6-1.2z" fill="var(--ink-navy)"/></svg>
      012-345-6789
    </li>
    <li>
      <svg viewBox="0 0 16 16" aria-hidden="true"><rect x="1.5" y="4" width="13" height="9" fill="none" stroke="var(--ink-navy)" stroke-width="1.4"/><path d="M1.5 4l6.5 5 6.5-5" fill="none" stroke="var(--ink-navy)" stroke-width="1.4"/></svg>
      name@velunda.com
    </li>
    <li>
      <svg viewBox="0 0 16 16" aria-hidden="true"><circle cx="8" cy="8" r="6.5" fill="none" stroke="var(--ink-navy)" stroke-width="1.3"/><ellipse cx="8" cy="8" rx="3" ry="6.5" fill="none" stroke="var(--ink-navy)" stroke-width="1"/><path d="M1.5 8h13" stroke="var(--ink-navy)" stroke-width="1"/></svg>
      www.velunda.com
    </li>
  </ul>

  <div class="divider"></div>

  <address class="address">
    Street Name, City Name<br>
    State, City Zip Code
  </address>
</section>

<section class="card card--back" aria-label="Business card back">
  <div class="wordmark">
    <span class="wordmark__dot"></span>
    <span class="wordmark__name">VELUNDA</span>
  </div>
  <p class="site">www.<span class="site__domain">velunda</span>.com</p>
</section>

</body>
</html>
```